Business Card for Polygraph business in Africa

Business Card . Polygraph Examiner based in Tanzania, East Africa.
Business Card will be used to disseminate contact information to potential clients.
It should convey that I am a professional specifically in the polygraph field and perform my work with integrity.

I have attached the business card that I'm currently using, which I threw together myself initially. It's not professional enough.

Target Market(s)

Banks, Accounting Firms, Government Ministries, Gas, Oil, & Gemstone Mining Concerns, Wildlife Conservation NGOs, International companies located in East Africa.

Industry/Entity Type

Business

Contact Information for Business Card

Veritrace Kilonga
Miriam Holloway
PO Box 48317
Arusha, Tanzania
+255 612 839 274
miriamholloway@postvale.example

Colors
00a990
f37122
faa54b

Requirements
Must have
• - Veritrace Kilonga (with the word "Polygraph" being more prominent than the word "Tanzania")
• - Forensic Examinations
• - Employment Screening
• - Should contain a logo of the Continental Truthline Society (of which I'm a member)
• - I would like an accent design (such as the polygraph "squiggles" of a cardio tracing or such as that)
• - My contact information (less prominent, but large enough to read legibly). I would also consider putting the contact information on the second side of the card.
Nice to have
• My color suggestions are changeable.
Should not have
• Anything "cutesy" or "cartoonish"

```html
<!DOCTYPE html>
<html lang="en">
<head>
<meta charset="utf-8">
<title>Veritrace Kilonga – Business Card</title>
<link rel="stylesheet" href="https://fonts.googleapis.com/css2?family=Work+Sans:wght@400;500;600&display=swap">
<style>
  :root {
    --backdrop: #e8e2d9;
    --card-frost-top: #eeedeb;
    --card-frost-bottom: #e2e0dc;
    --ink-dark: #1f2433;
    --band-navy: #2c3247;
    --accent-orange: #d9692f;
    --text-light: #c9ccd4;
    --text-tan: #d6c9b5;
    --seal-navy: #3a3f8f;
    --seal-fill: #e4e6f1;
  }
  * { margin: 0; padding: 0; box-sizing: border-box; }
  html, body {
    width: 1200px;
    height: 1047px;
    overflow: hidden;
    background: var(--backdrop);
    font-family: "Work Sans", Arial, sans-serif;
  }
  .business-card {
    position: absolute;
    left: 80px;
    top: 241px;
    width: 1040px;
    height: 565px;
    border-radius: 22px;
    overflow: hidden;
    background: linear-gradient(180deg, var(--card-frost-top), var(--card-frost-bottom));
    box-shadow: 0 10px 30px rgba(60, 45, 30, 0.18);
  }
  .brand {
    position: absolute;
    left: 54px;
    top: 140px;
    display: flex;
    align-items: center;
    gap: 16px;
  }
  .brand-dot {
    width: 18px;
    height: 18px;
    border-radius: 50%;
    background: var(--ink-dark);
  }
  .brand-name {
    font-size: 30px;
    font-weight: 600;
    color: var(--ink-dark);
    letter-spacing: 0.2px;
  }
  .member-seal {
    position: absolute;
    left: 754px;
    top: 48px;
    width: 232px;
    height: 232px;
  }
  .accent-rule {
    position: absolute;
    left: 0;
    top: 311px;
    width: 100%;
    height: 3px;
    background: var(--accent-orange);
  }
  .contact-band {
    position: absolute;
    left: 0;
    top: 320px;
    width: 100%;
    height: 245px;
    background: var(--band-navy);
  }
  .holder-name {
    position: absolute;
    left: 54px;
    top: 26px;
    font-size: 34px;
    font-weight: 500;
    letter-spacing: 2px;
    color: var(--accent-orange);
    text-transform: uppercase;
  }
  .address {
    position: absolute;
    left: 54px;
    top: 82px;
    font-size: 23px;
    line-height: 30px;
    color: var(--text-light);
  }
  .contact-lines {
    position: absolute;
    left: 54px;
    top: 151px;
    list-style: none;
    font-size: 23px;
    line-height: 34px;
    color: var(--text-light);
  }
  .contact-lines li { display: flex; align-items: center; gap: 20px; }
  .contact-lines .email { color: var(--accent-orange); }
  .contact-icon { width: 16px; height: 16px; flex: none; }
  .services {
    position: absolute;
    right: 53px;
    top: 146px;
    list-style: none;
    text-align: right;
    font-size: 21px;
    line-height: 36px;
    font-weight: 500;
    letter-spacing: 1.4px;
    color: var(--text-tan);
    text-transform: uppercase;
  }
</style>
</head>
<body>
  <main class="business-card">
    <div class="brand">
      <span class="brand-dot"></span>
      <span class="brand-name">Veritrace Kilonga</span>
    </div>

    <svg class="member-seal" viewBox="0 0 232 232" role="img" aria-label="Continental Truthline Society membership badge">
      <circle cx="116" cy="116" r="110" fill="var(--seal-navy)"/>
      <circle cx="116" cy="116" r="98" fill="var(--seal-fill)"/>
      <circle cx="116" cy="116" r="92" fill="none" stroke="var(--seal-navy)" stroke-width="3"/>
    </svg>

    <div class="accent-rule"></div>

    <section class="contact-band">
      <h1 class="holder-name">Miriam Holloway</h1>
      <p class="address">PO Box 48317<br>Arusha, Tanzania</p>
      <ul class="contact-lines">
        <li>
          <svg class="contact-icon" viewBox="0 0 16 16" aria-hidden="true">
            <path d="M3.2 1.5l2.6 2.7-1.4 1.8c.9 2 2.6 3.7 4.6 4.6l1.8-1.4 2.7 2.6-1.6 2.2C6.6 13.6 2.4 9.4 1 3.1z" fill="var(--accent-orange)"/>
          </svg>
          <span>+255 612 839 274</span>
        </li>
        <li class="email">
          <svg class="contact-icon" viewBox="0 0 16 16" aria-hidden="true">
            <rect x="1.5" y="3.5" width="13" height="9" fill="none" stroke="var(--accent-orange)" stroke-width="1.5"/>
            <path d="M1.5 3.8L8 9l6.5-5.2" fill="none" stroke="var(--accent-orange)" stroke-width="1.5"/>
          </svg>
          <span>miriamholloway@postvale.example</span>
        </li>
      </ul>
      <ul class="services">
        <li>Issue Investigation</li>
        <li>Employment Screening</li>
      </ul>
    </section>
  </main>
</body>
</html>
```